MRT Property - Business Cards

Looking for a business card & general letterhead, signage etc design for our new logo.

Colours:
000a20
0056a2
00b5ef
0088ce
68cef2

Fonts:
Poppins
Karla

Please keep look and feel of new brand - example in the zip package I sent.

```html
<!DOCTYPE html>
<html lang="en">
<head>
<meta charset="utf-8">
<title>MRT Property – Business Cards</title>
<link rel="stylesheet" href="https://fonts.googleapis.com/css2?family=Poppins:wght@300;400;600;700&family=Sue+Ellen+Francisco&display=swap">
<style>
  :root {
    --ink: #000a20;
    --navy: #0056a2;
    --sky: #00b5ef;
    --ocean: #0088ce;
    --mist: #68cef2;
    --paper: #ffffff;
    --stage: #e9ecef;
  }
  * { margin: 0; padding: 0; box-sizing: border-box; }
  html, body { width: 1200px; height: 931px; overflow: hidden; }
  body {
    background: var(--stage);
    font-family: "Poppins", sans-serif;
    color: var(--ink);
    position: relative;
  }
  .card {
    position: absolute;
    width: 560px;
    height: 320px;
    border-radius: 18px;
    overflow: hidden;
    box-shadow: 0 14px 30px rgba(0, 10, 32, 0.22);
  }

  /* Back side */
  .card-back {
    left: 60px;
    top: 70px;
    background: var(--navy);
  }
  .back-pattern {
    position: absolute;
    inset: 0;
    background: linear-gradient(100deg, var(--sky) 0%, var(--ocean) 30%, var(--navy) 60%, #0d3f86 100%);
  }
  .back-brand {
    position: absolute;
    right: 64px;
    top: 150px;
    display: flex;
    align-items: center;
    gap: 10px;
    font-weight: 700;
    font-size: 30px;
    color: var(--paper);
    letter-spacing: 0.5px;
  }
  .brand-dot {
    width: 26px; height: 26px;
    border-radius: 50%;
    background: var(--mist);
  }

  /* Front side */
  .card-front {
    left: 580px;
    top: 540px;
    background: var(--paper);
  }
  .front-brand {
    position: absolute;
    right: 44px;
    top: 44px;
    display: flex;
    align-items: center;
    gap: 14px;
    font-weight: 700;
    font-size: 44px;
    color: var(--navy);
    letter-spacing: 0.5px;
  }
  .front-brand .brand-dot { width: 44px; height: 44px; background: var(--ocean); }
  .rule {
    position: absolute;
    left: 40px;
    right: 44px;
    top: 150px;
    height: 2px;
    background: var(--navy);
  }
  .person {
    position: absolute;
    left: 40px;
    top: 164px;
  }
  .person-name {
    font-family: "Sue Ellen Francisco", cursive;
    font-size: 38px;
    line-height: 1;
    color: var(--ink);
  }
  .person-role {
    font-size: 13px;
    font-weight: 400;
    color: var(--ink);
    margin-top: 2px;
  }
  .contacts {
    position: absolute;
    left: 40px;
    top: 232px;
    list-style: none;
    font-size: 13px;
    line-height: 20px;
  }
  .contacts li { display: flex; align-items: center; gap: 10px; }
  .contacts svg { width: 13px; height: 13px; fill: var(--navy); flex: none; }
  .address {
    position: absolute;
    right: 44px;
    top: 176px;
    font-size: 13px;
    line-height: 19px;
    text-align: right;
  }
  .band {
    position: absolute;
    left: 0; right: 0; bottom: 0;
    height: 14px;
    display: flex;
  }
  .band span { flex: 1; }
  .band .b1 { background: var(--mist); }
  .band .b2 { background: var(--sky); }
  .band .b3 { background: var(--ocean); }
  .band .b4 { background: var(--navy); }
</style>
</head>
<body>
  <section class="card card-back" aria-label="Card back">
    <div class="back-pattern" role="img" aria-label="Repeating brand symbol pattern in blue tones"></div>
    <div class="back-brand"><span class="brand-dot"></span>MRT Property</div>
  </section>

  <section class="card card-front" aria-label="Card front">
    <div class="front-brand"><span class="brand-dot"></span>MRT Property</div>
    <div class="rule"></div>

    <div class="person">
      <p class="person-name">Daniel Carter</p>
      <p class="person-role">Managing Director</p>
    </div>

    <ul class="contacts">
      <li>
        <svg viewBox="0 0 24 24"><path d="M6.6 10.8a15.1 15.1 0 0 0 6.6 6.6l2.2-2.2c.3-.3.7-.4 1-.2 1.1.4 2.3.6 3.6.6.6 0 1 .4 1 1V20c0 .6-.4 1-1 1A17 17 0 0 1 3 4c0-.6.4-1 1-1h3.5c.6 0 1 .4 1 1 0 1.3.2 2.5.6 3.6.1.3 0 .7-.2 1z"/></svg>
        1 (555) 014-2290
      </li>
      <li>
        <svg viewBox="0 0 24 24"><path d="M2 5h20v14H2z M2 5l10 8 10-8" stroke="#fff" stroke-width="1.5"/></svg>
        info@mrtproperty.com
      </li>
      <li>
        <svg viewBox="0 0 24 24"><circle cx="12" cy="12" r="10"/><path d="M2 12h20M12 2c3 3 3 17 0 20M12 2c-3 3-3 17 0 20" stroke="#fff" stroke-width="1.3" fill="none"/></svg>
        www.mrtproperty.com
      </li>
    </ul>

    <p class="address">482 Maple Ridge Ave Suite<br>210 Dayton Ohio 45402</p>

    <div class="band"><span class="b1"></span><span class="b2"></span><span class="b3"></span><span class="b4"></span></div>
  </section>
</body>
</html>
```